Income Tax Business Cards - Updates

Need to update these business cards while keeping all the same wording but just update them and make them look nicer and more modern/ on brand with our brand.

Industry/Entity Type

finance

Contact Information for Business Card

we have multiple locations so will just need to easily be able to change the address and phone numbers

Colors

Designer to choose colors to be used in the design.

```html
<!DOCTYPE html>
<html lang="en">
<head>
<meta charset="utf-8">
<title>Ledgerline Financial Group – Business Cards</title>
<link href="https://fonts.googleapis.com/css2?family=Montserrat:wght@400;500;700;800&display=swap" rel="stylesheet">
<style>
  :root {
    --green: #0f5230;
    --green-deep: #0b4326;
    --red: #c61f2a;
    --white: #ffffff;
    --backdrop: #2b2b2d;
  }
  * { box-sizing: border-box; margin: 0; padding: 0; }
  html, body { width: 1200px; height: 900px; overflow: hidden; }
  body {
    background: var(--backdrop);
    font-family: "Montserrat", sans-serif;
    position: relative;
  }
  .card {
    position: absolute;
    width: 630px;
    height: 360px;
    border-radius: 22px;
    overflow: hidden;
    background: var(--green);
    box-shadow: 0 14px 30px rgba(0,0,0,.45);
  }
  .card--front { left: 285px; top: 65px; }
  .card--back  { left: 285px; top: 475px; }

  /* Brand name set as text */
  .brand { position: absolute; text-align: center; line-height: 1; }
  .brand__mark {
    display: inline-block; width: 16px; height: 16px; border-radius: 50%;
    background: currentColor; vertical-align: middle; margin-right: 10px;
  }
  .brand__name { font-weight: 700; font-size: 38px; letter-spacing: .5px; vertical-align: middle; }
  .brand__sub { display: block; font-weight: 700; font-size: 38px; letter-spacing: .5px; margin-top: 6px; }

  .card--front .brand { left: 0; right: 0; top: 62px; color: var(--white); }
  .card--front .brand__name, .card--front .brand__sub { font-size: 34px; }

  .pill {
    position: absolute; left: 50%; top: 196px; transform: translateX(-50%);
    background: var(--red); color: var(--white);
    font-weight: 700; font-size: 17px; letter-spacing: .8px;
    padding: 7px 22px; border-radius: 20px; white-space: nowrap;
  }
  .front-offer {
    position: absolute; left: 0; right: 0; bottom: 58px; text-align: center;
    color: var(--white); font-weight: 800; font-size: 27px; letter-spacing: 1.5px;
  }
  .amount { color: var(--red); }

  /* Back */
  .back-curve { position: absolute; inset: 0; }
  .card--back .brand { left: 360px; right: 22px; top: 112px; color: var(--green); }
  .card--back .brand__name, .card--back .brand__sub { font-size: 27px; }

  .contact {
    position: absolute; left: 40px; top: 36px; color: var(--white);
    font-weight: 500; font-size: 15px; line-height: 1.4; letter-spacing: .5px;
  }
  .contact__phone {
    display: flex; align-items: center; gap: 8px;
    font-weight: 700; font-size: 19px; margin-top: 4px;
  }
  .contact__phone svg { width: 15px; height: 15px; }
  .back-offer {
    position: absolute; left: 36px; top: 178px; color: var(--white);
    font-weight: 800; line-height: 1.05; letter-spacing: 1px;
  }
  .back-offer__lead { font-size: 36px; }
  .back-offer__sub { font-size: 25px; margin-top: 4px; }
  .back-note {
    position: absolute; left: 38px; bottom: 34px; color: var(--white);
    font-weight: 600; font-size: 13px; letter-spacing: .8px;
  }
  .back-note .divider { color: var(--red); margin: 0 6px; }
</style>
</head>
<body>

  <section class="card card--front">
    <div class="brand">
      <span class="brand__mark"></span><span class="brand__name">Ledgerline</span>
      <span class="brand__sub">Financial Group</span>
    </div>
    <div class="pill">FILE YOUR TAXES HERE</div>
    <p class="front-offer">UP TO <span class="amount">&amp;6000</span> SAME DAY ADVANCE</p>
  </section>

  <section class="card card--back">
    <svg class="back-curve" viewBox="0 0 630 360" aria-hidden="true">
      <path d="M372 0 C300 110 360 290 630 352 L630 0 Z" fill="var(--red)"/>
      <path d="M386 0 C318 110 378 280 630 338 L630 0 Z" fill="var(--white)"/>
    </svg>

    <div class="brand">
      <span class="brand__mark"></span><span class="brand__name">Ledgerline</span>
      <span class="brand__sub">Financial Group</span>
    </div>

    <address class="contact" style="font-style:normal">
      781 Marlow Street<br>
      Ste 310<br>
      Country Name AB 4172
      <span class="contact__phone">
        <svg viewBox="0 0 24 24" aria-hidden="true"><path fill="var(--red)" d="M6.6 10.8a15.1 15.1 0 0 0 6.6 6.6l2.2-2.2a1 1 0 0 1 1-.25 11.4 11.4 0 0 0 3.6.57 1 1 0 0 1 1 1V20a1 1 0 0 1-1 1A17 17 0 0 1 3 4a1 1 0 0 1 1-1h3.5a1 1 0 0 1 1 1c0 1.25.2 2.45.57 3.57a1 1 0 0 1-.25 1z"/></svg>
        (555) 014-2290
      </span>
    </address>

    <div class="back-offer">
      <div class="back-offer__lead">UP TO <span class="amount">&amp;6000</span></div>
      <div class="back-offer__sub">SAME DAY ADVANCE</div>
    </div>

    <p class="back-note">FREE ESTIMATES!<span class="divider">/</span>ON APPROVED TAX RETURNS!</p>
  </section>

</body>
</html>
```